Silver Harbor Med Spa Membership Sales Presentation to Clients handout

Hello! We are a high tech, Silver Harbor Med Spa in Dallas Texas that won Best Med Spa in Addison. I want my graphic membership form to represent that. We serve women and men so want it neutral but show cutting edge. Our colors are black, white, gray but would entertain your view. Having a challenge on making it easy to read as each membership gets more services yet one service a month. Thought maybe colorcoding what services are together? Definite road blocks on my end. I used Canva to lay out, but as you can see I am NOT gifted at graphic design. ;))

Target Market(s)

39-69

Industry/Entity Type

Medical Med Spa

Requirements
Must have
• cutting edge look

```html
<!DOCTYPE html>
<html lang="en">
<head>
<meta charset="utf-8">
<title>Silver Harbor Med Spa – Ageless Glow Memberships</title>
<link href="https://fonts.googleapis.com/css2?family=Lato:ital,wght@0,400;0,700;0,900;1,400&family=Libre+Baskerville:wght@700&display=swap" rel="stylesheet">
<style>
  :root{
    --stage:#121212;
    --paper:#ffffff;
    --panel:#e8e9ea;
    --teal:#50c4c2;
    --ink:#1e2a2e;
    --text:#2a2d2f;
    --black:#111111;
    --good:#a6dff4;
    --better:#93b1f3;
    --best:#86d9cf;
    --good-mark:#5cc6ea;
    --better-mark:#4f78e0;
    --best-mark:#33b9a9;
    --band-1:#95e2b5;
    --band-2:#b6f0b2;
    --band-3:#cdf6cd;
    --band-4:#b6ead8;
    --band-5:#a9d9e8;
    --band-6:#9ec9f1;
    --band-7:#86aff5;
    --award:#c8202a;
  }
  *{box-sizing:border-box;margin:0;padding:0}
  html,body{width:1200px;height:1200px;overflow:hidden;background:var(--stage)}
  body{position:relative;font-family:"Lato",sans-serif;color:var(--text)}
  .flyer{position:absolute;left:160px;top:30px;width:660px;height:855px;transform:scale(1.33334);transform-origin:0 0;overflow:hidden;background:var(--panel)}
  .backdrop{position:absolute;inset:0;width:660px;height:855px}
  .brand{position:absolute;left:30px;top:38px;width:150px;text-align:center;font-family:"Lato",sans-serif;font-weight:400;font-size:19px;line-height:1.15;letter-spacing:1.5px;text-transform:uppercase;color:var(--ink)}
  .title{position:absolute;right:23px;top:18px;text-align:right;font-family:"Lato",sans-serif;font-weight:400;font-size:35px;line-height:36px;color:var(--ink);letter-spacing:.3px}
  .treatment-head{position:absolute;left:24px;top:125px;width:276px;height:26px;color:#fff;font-weight:900;font-size:15px;letter-spacing:3px;display:flex;align-items:center;justify-content:center;padding-right:20px}
  .treatment-note{position:absolute;left:24px;top:153px;width:256px;text-align:center;font-style:italic;font-size:12px;color:var(--text)}
  .plan{position:absolute;top:125px;height:52px;text-align:center;font-weight:900}
  .plan-name{height:25px;line-height:25px;font-size:14px;color:var(--ink)}
  .plan-price{height:27px;line-height:27px;background:var(--black);font-size:14px}
  .plan.good{left:417px;width:66px}.plan.good .plan-name{background:var(--good)}.plan.good .plan-price{color:var(--good)}
  .plan.better{left:493px;width:66px}.plan.better .plan-name{background:var(--better)}.plan.better .plan-price{color:var(--better)}
  .plan.best{left:569px;width:68px}.plan.best .plan-name{background:var(--best)}.plan.best .plan-price{color:var(--best)}
  .row{position:absolute;left:0;width:660px}
  .items{position:absolute;left:54px;top:0;height:100%;display:flex;flex-direction:column;justify-content:center;list-style:none}
  .items li{height:15px;line-height:15px;font-size:11.5px;font-weight:700;color:var(--text);white-space:nowrap}
  .unlimited{position:absolute;left:24px;top:0;width:18px;height:100%;display:flex;align-items:center;justify-content:center}
  .unlimited span{transform:rotate(-90deg);color:#fff;font-size:10px;font-weight:900;letter-spacing:1.5px;white-space:nowrap}
  .cell{position:absolute;top:0;height:100%;background:var(--paper);display:flex;flex-direction:column;justify-content:center;align-items:center}
  .cell.good{left:417px;width:66px;color:var(--good-mark)}
  .cell.better{left:493px;width:66px;color:var(--better-mark)}
  .cell.best{left:569px;width:68px;color:var(--best-mark)}
  .mark{height:15px;width:20px;display:flex;align-items:center;justify-content:center}
  .tick::after{content:"";display:block;width:5px;height:9px;border-right:2px solid currentColor;border-bottom:2px solid currentColor;transform:translateY(-1px) rotate(40deg)}
  .dash::after{content:"";display:block;width:7px;height:2px;background:currentColor;opacity:.8}
  .cell.discount{justify-content:flex-end;padding-bottom:40px;font-family:"Libre Baskerville",serif;font-weight:700;font-size:19px;line-height:23px;text-align:center;color:var(--ink)}
  .cell.discount.good{background:linear-gradient(to bottom,#fff 25%,var(--good) 100%)}
  .cell.discount.better{background:linear-gradient(to bottom,#fff 25%,var(--better) 100%)}
  .cell.discount.best{background:linear-gradient(to bottom,#fff 25%,var(--best) 100%)}
  .footer{position:absolute;left:0;top:820px;width:660px;height:35px;background:var(--teal);display:flex;align-items:center;padding-left:22px;font-size:12.5px;font-weight:700;color:var(--black)}
  .contact{display:flex;align-items:center;gap:6px;margin-right:18px}
  .contact svg{width:16px;height:16px;flex:none}
</style>
</head>
<body>
<div class="flyer">
  <svg class="backdrop" viewBox="0 0 660 855" aria-hidden="true">
    <defs>
      <clipPath id="band-edge">
        <path d="M0 170 L338 170 C360 240 380 330 384 420 C390 520 395 600 388 660 C382 730 372 780 362 812 L0 812 Z"/>
      </clipPath>
    </defs>
    <rect width="660" height="855" fill="var(--panel)"/>
    <path d="M187 0 H660 V107 H278 Q238 45 187 0 Z" fill="var(--teal)"/>
    <path d="M0 0 H187 Q238 45 278 107 C335 240 415 430 412 600 C410 700 400 780 392 820 H0 Z" fill="var(--paper)"/>
    <circle cx="232" cy="50" r="38" fill="var(--award)"/>
    <path d="M24 125 H290 L300 151 H24 Z" fill="var(--black)"/>
    <g clip-path="url(#band-edge)">
      <rect x="22" y="177" width="420" height="90" fill="var(--band-1)"/>
      <rect x="22" y="280" width="420" height="108" fill="var(--band-2)"/>
      <rect x="22" y="402" width="420" height="28" fill="var(--band-3)"/>
      <rect x="22" y="442" width="420" height="80" fill="var(--band-4)"/>
      <rect x="22" y="537" width="420" height="25" fill="var(--band-5)"/>
      <rect x="22" y="572" width="420" height="53" fill="var(--band-6)"/>
      <rect x="22" y="635" width="420" height="170" fill="var(--band-7)"/>
    </g>
    <rect x="24" y="177" width="18" height="90" fill="var(--black)"/>
  </svg>

  <div class="brand">Silver Harbor<br>Med Spa</div>
  <h1 class="title">AGELESS GLOW<br>MEMBERSHIPS</h1>

  <div class="treatment-head">TREATMENT</div>
  <p class="treatment-note">(Choose 1 color per month)</p>

  <div class="plan good"><div class="plan-name">GOOD</div><div class="plan-price">$189</div></div>
  <div class="plan better"><div class="plan-name">BETTER</div><div class="plan-price">$289</div></div>
  <div class="plan best"><div class="plan-name">BEST</div><div class="plan-price">$389</div></div>

  <section class="row" style="top:177px;height:90px">
    <div class="unlimited"><span>UNLIMITED</span></div>
    <ul class="items"><li>SKIN EVALUATION</li><li>INFRARED SAUNA</li><li>MASSAGE CHAIR</li><li>VIBRATIONAL LYMPHATIC PLATE</li><li>CONTORA TARGETED WEIGHT LOSS</li></ul>
    <div class="cell good"><i class="mark tick"></i><i class="mark tick"></i><i class="mark tick"></i><i class="mark tick"></i><i class="mark dash"></i></div>
    <div class="cell better"><i class="mark tick"></i><i class="mark tick"></i><i class="mark tick"></i><i class="mark tick"></i><i class="mark dash"></i></div>
    <div class="cell best"><i class="mark tick"></i><i class="mark tick"></i><i class="mark tick"></i><i class="mark tick"></i><i class="mark tick"></i></div>
  </section>

  <section class="row" style="top:280px;height:108px">
    <ul class="items"><li>MEDICAL FACIAL</li><li>FACE LYMPHATIC DRAINAGE</li><li>RED LIGHT THERAPY</li><li>PH OXYGEN SERUM</li><li>DERMAPLANING</li><li>VITAMIN A PEEL</li></ul>
    <div class="cell good"><i class="mark tick"></i><i class="mark tick"></i><i class="mark tick"></i><i class="mark tick"></i><i class="mark dash"></i><i class="mark dash"></i></div>
    <div class="cell better"><i class="mark tick"></i><i class="mark tick"></i><i class="mark tick"></i><i class="mark tick"></i><i class="mark dash"></i><i class="mark dash"></i></div>
    <div class="cell best"><i class="mark tick"></i><i class="mark tick"></i><i class="mark tick"></i><i class="mark tick"></i><i class="mark tick"></i><i class="mark tick"></i></div>
  </section>

  <section class="row" style="top:402px;height:28px">
    <ul class="items"><li>CHEMICAL PEEL VIREO ITALIAN</li></ul>
    <div class="cell good"><i class="mark dash"></i></div>
    <div class="cell better"><i class="mark dash"></i></div>
    <div class="cell best"><i class="mark tick"></i></div>
  </section>

  <section class="row" style="top:442px;height:80px">
    <ul class="items"><li>LUMARA LIGHT RENEWAL</li><li>LUMARA 2 CORRECTION PASSES</li><li>LUMARA UP TO 10 CORRECTION PASSES</li><li>LUMARA HAIR REMOVAL</li></ul>
    <div class="cell good"><i class="mark tick"></i><i class="mark tick"></i><i class="mark dash"></i><i class="mark dash"></i></div>
    <div class="cell better"><i class="mark tick"></i><i class="mark tick"></i><i class="mark tick"></i><i class="mark tick"></i></div>
    <div class="cell best"><i class="mark tick"></i><i class="mark tick"></i><i class="mark tick"></i><i class="mark tick"></i></div>
  </section>

  <section class="row" style="top:537px;height:25px">
    <ul class="items"><li>LUMARA SKIN TIGHTEN</li></ul>
    <div class="cell good"><i class="mark dash"></i></div>
    <div class="cell better"><i class="mark dash"></i></div>
    <div class="cell best"><i class="mark tick"></i></div>
  </section>

  <section class="row" style="top:572px;height:53px">
    <ul class="items"><li>MICRONEEDLING</li><li>MICRONEEDLING PDO RADIANCE</li></ul>
    <div class="cell good"><i class="mark dash"></i><i class="mark dash"></i></div>
    <div class="cell better"><i class="mark tick"></i><i class="mark dash"></i></div>
    <div class="cell best"><i class="mark tick"></i><i class="mark tick"></i></div>
  </section>

  <section class="row" style="top:635px;height:170px">
    <ul class="items"><li>LASER RESURFACING</li><li>CHEMICAL PEELS PROGRESSIVE OR MID DEPTH</li><li>PLASMA PEN</li><li>HYPERBARIC OXYGEN</li><li>MASSAGE</li><li>AIRBRUSH TANNING</li><li>IONIC DETOX</li><li>LYMPHATIC DRAINAGE</li><li>TIRZEPATIDE WEIGHT LOSS PEPTIDE</li><li>LIP FILLERS NEEDLE LESS</li></ul>
    <div class="cell discount good">10%<br>OFF</div>
    <div class="cell discount better">20%<br>OFF</div>
    <div class="cell discount best">30%<br>OFF</div>
  </section>

  <footer class="footer">
    <span class="contact">
      <svg viewBox="0 0 16 16" aria-hidden="true"><circle cx="8" cy="8" r="8" fill="var(--black)"/><path d="M5.2 4.2 L6.6 4 L7.3 5.9 L6.4 6.7 C6.9 7.8 7.9 8.9 9.1 9.5 L9.9 8.6 L11.8 9.3 L11.6 10.8 C11.5 11.3 11 11.6 10.5 11.5 C7.4 11 5 8.6 4.5 5.4 C4.4 4.8 4.7 4.3 5.2 4.2 Z" fill="#fff"/></svg>
      214 555 0147
    </span>
    <span class="contact">
      <svg viewBox="0 0 16 16" aria-hidden="true"><circle cx="8" cy="8" r="8" fill="var(--black)"/><path d="M8 3.3 C6.2 3.3 5 4.6 5 6.2 C5 8.4 8 12.4 8 12.4 C8 12.4 11 8.4 11 6.2 C11 4.6 9.8 3.3 8 3.3 Z" fill="#fff"/><circle cx="8" cy="6.2" r="1.2" fill="var(--black)"/></svg>
      1180 WILLOW BEND LN. PLANO, TX 75093
    </span>
    <span class="contact">
      <svg viewBox="0 0 16 16" aria-hidden="true"><circle cx="8" cy="8" r="8" fill="var(--black)"/><g fill="none" stroke="#fff" stroke-width="1"><circle cx="8" cy="8" r="4.3"/><ellipse cx="8" cy="8" rx="1.9" ry="4.3"/><path d="M3.7 8 H12.3"/></g></svg>
      SILVERHARBORMEDSPA.COM
    </span>
  </footer>
</div>
</body>
</html>
```